Brimlow OrthoLink IT Inc. new website

i need a website for my company which is dedicated to installation and service of computer systems in Dental Offices. I would like for it to encompass a technology feel and professional look. The company deals with all aspects of technology like, Audio Visual, computer systems and networks, Cloud services like data backup, data center. We provide manage services, support and services to Dental Professionals.
Updates

Looking for a Technology font but professional look Added Wednesday, April 20, 2016

Target Market(s)

Dental, Dentist

Industry/Entity Type

Dental

Number of Pages Required

5+ page

Font styles to use
Other font styles liked:
• Futuristic or Techy

Colors
0255a3
ec1f27

Requirements
Must have
• Tabs
Nice to have
• Have no idea maybe some suggestion on your part may help
Should not have
• A professional feel but have a techy look

```html
<!DOCTYPE html>
<html lang="en">
<head>
<meta charset="utf-8">
<title>Brimlow OrthoLink IT Inc.</title>
<link href="https://fonts.googleapis.com/css2?family=Raleway:wght@400;500;600;800&family=Open+Sans:wght@400;600&display=swap" rel="stylesheet">
<style>
:root{
  --red:#ec1f27;
  --blue:#0255a3;
  --ink:#1e1e1e;
  --muted:#8a8a8a;
  --line:#d6d6d6;
  --footer:#333333;
  --white:#ffffff;
}
*{box-sizing:border-box;margin:0;padding:0}
html,body{width:1200px;height:3956px;overflow:hidden}
body{position:relative;background:var(--white);font-family:"Open Sans",Arial,sans-serif;color:var(--ink)}
section,header,footer{position:absolute;left:0;width:1200px}
.abs{position:absolute}
.center{left:0;width:1200px;text-align:center}
.section-title{font-family:"Raleway",Arial,sans-serif;font-weight:500;font-size:40px;letter-spacing:1px;text-transform:uppercase;color:var(--ink)}
.section-title span{color:var(--red)}
.section-sub{font-size:15px;color:var(--muted)}
.btn{position:absolute;background:var(--red);color:var(--white);font-size:16px;text-transform:uppercase;display:flex;align-items:center;justify-content:center;font-family:"Open Sans",Arial,sans-serif}
.body-text{font-size:14px;line-height:1.55;color:#777}

/* header */
.site-header{top:0;height:105px;background:var(--white)}
.brand{left:79px;top:30px;font-family:"Raleway",Arial,sans-serif;font-weight:800;font-size:30px;color:var(--blue)}
.main-nav{right:80px;top:40px;display:flex;gap:42px;font-size:16px;text-transform:uppercase;color:var(--ink)}
.main-nav .active{position:relative}
.main-nav .active::after{content:"";position:absolute;left:8px;right:8px;top:30px;height:5px;background:var(--ink)}

/* hero */
.hero{top:105px;height:575px}
.hero-photo{inset:0;background:linear-gradient(135deg,#c9cdd0 0%,#8d9296 45%,#b7bbbe 100%)}
.hero-title{top:95px;font-family:"Raleway",Arial,sans-serif;font-weight:800;font-size:64px;line-height:74px;color:var(--white);text-transform:uppercase}
.hero-text{top:262px;font-size:21px;line-height:28px;color:var(--white)}
.hero-rule{top:356px;left:382px;width:436px;height:5px;background:var(--white)}

/* services */
.services{top:680px;height:612px}
.service{width:340px;text-align:center}
.service-icon{width:148px;height:148px;border-radius:50%;background:var(--red);border:5px solid #4a4a4a;margin:0 auto;display:flex;align-items:center;justify-content:center}
.service h3{font-family:"Raleway",Arial,sans-serif;font-weight:500;font-size:19px;text-transform:uppercase;margin-top:26px;line-height:24px;height:52px}
.service p{margin-top:22px;font-size:14px;line-height:22px;color:#777}

/* who we are */
.about{top:1292px;height:470px}
.about-photo{inset:0;background:linear-gradient(90deg,#1b1d1f 0%,#2c3134 55%,#3d4447 100%)}
.about-laptop{left:171px;top:185px;width:422px;height:224px;background:linear-gradient(135deg,#3b78b8,#7fb0d9 55%,#dfe3e6);border-radius:6px}
.about-text{left:667px;top:193px;width:441px;font-size:14px;line-height:22px;color:#e6e6e6}

/* blog */
.blog{top:1762px;height:564px}
.post{width:333px;top:168px}
.post-photo{height:188px}
.post h4{margin-top:22px;font-size:19px;font-weight:400;line-height:27px}
.post-meta{margin-top:10px;font-size:14px;color:var(--red);display:flex;gap:14px;align-items:center}
.post-meta .sep{color:#aaa}
.post p{margin-top:10px;font-size:14px;line-height:22px;color:#777}

/* testimonials */
.clients{top:2326px;height:469px}
.clients-photo{inset:0;background:linear-gradient(180deg,#4a4541 0%,#2f2b28 100%)}
.client-name{top:275px;font-size:20px;font-weight:600;color:var(--white);letter-spacing:1px}
.client-role{top:302px;font-size:15px;color:var(--red)}
.quote{top:340px;left:230px;width:740px;font-size:14px;line-height:22px;color:var(--white);text-align:center}
.quote-mark{font-family:Georgia,serif;font-size:64px;color:var(--red);line-height:1}

/* partner strip */
.partners{top:2795px;height:145px;display:flex;align-items:center;justify-content:space-around;padding:0 70px}
.partners span{font-family:"Raleway",Arial,sans-serif;font-weight:600;font-size:20px;color:#555}

/* newsletter */
.newsletter{top:2940px;height:317px}
.newsletter-photo{inset:0;background:linear-gradient(135deg,#3a3f44 0%,#23272b 100%)}
.nl-input{left:319px;top:211px;width:396px;height:53px;background:var(--white);font-size:14px;color:#999;padding:0 18px;display:flex;align-items:center}

/* contact */
.contact{top:3257px;height:488px}
.contact-info{left:90px;width:310px;text-align:center;font-size:17px;color:var(--ink)}
.field{position:absolute;border:1px solid var(--line);font-size:13px;color:#aaa;padding:14px 16px}

/* footer */
.site-footer{top:3745px;height:211px;background:var(--footer);color:#cfcfcf;font-size:13px}
.foot-brand{left:92px;top:38px;width:240px;text-align:center;font-family:"Raleway",Arial,sans-serif;font-weight:800;font-size:20px;color:var(--white)}
.socials{left:172px;top:106px;display:flex;gap:18px}
.socials span{width:14px;height:14px;border-radius:50%;background:var(--red)}
.copyright{left:72px;top:134px;width:280px;text-align:center;font-size:12px;line-height:16px;color:var(--white)}
.copyright b{color:var(--red);font-weight:400}
.foot-col h5{font-size:15px;font-weight:400;color:var(--red);text-transform:uppercase;margin-bottom:10px}
.foot-col li{list-style:none;line-height:31px}
.foot-col li.on{color:var(--white)}
</style>
</head>
<body>

<header class="site-header">
  <div class="abs brand">Brimlow OrthoLink IT</div>
  <nav class="abs main-nav">
    <span class="active">Home</span><span>About</span><span>Services</span><span>Support</span><span>Client</span><span>Blog</span><span>Contact</span>
  </nav>
</header>

<section class="hero">
  <div class="abs hero-photo" role="img" aria-label="Photo of a desk with a laptop, keyboard, clipboard, glasses and a stethoscope"></div>
  <h1 class="abs center hero-title">Technology for best<br>dental practices</h1>
  <p class="abs center hero-text">We are an IT Company Focused on Dental IT Solutions, Computer<br>Systems &amp; Networks, Cloud Services of Data Backup</p>
  <div class="abs hero-rule"></div>
  <a class="btn" style="left:514px;top:409px;width:169px;height:53px">Learn More</a>
</section>

<section class="services">
  <h2 class="abs center section-title" style="top:50px">Our <span>Services</span></h2>
  <p class="abs center section-sub" style="top:108px">Lorem Ipsum is simply dummy text of the printing and typesetting industry.</p>

  <div class="abs service" style="left:75px;top:169px">
    <div class="service-icon">
      <svg width="70" height="60" viewBox="0 0 70 60" fill="none" stroke="#fff" stroke-width="3">
        <rect x="3" y="8" width="22" height="44"/><line x1="3" y1="18" x2="25" y2="18"/><line x1="3" y1="42" x2="25" y2="42"/>
        <path d="M32 22h8l10-10v36L40 38h-8z"/><path d="M56 20q6 10 0 20"/><path d="M61 14q11 16 0 32"/>
      </svg>
    </div>
    <h3>Audio Visual</h3>
    <p>Lorem Ipsum is simply dummy text of the printing and typesetting industry. Lorem Ipsum has been the industry's standard dummy text.</p>
  </div>

  <div class="abs service" style="left:431px;top:169px">
    <div class="service-icon">
      <svg width="70" height="60" viewBox="0 0 70 60" fill="none" stroke="#fff" stroke-width="3">
        <rect x="5" y="5" width="60" height="38"/><path d="M12 26h14l5-10 7 18 5-8h15"/><line x1="35" y1="43" x2="35" y2="52"/><line x1="22" y1="54" x2="48" y2="54"/>
      </svg>
    </div>
    <h3>Computer Systems &amp;<br>Networks</h3>
    <p>Lorem Ipsum is simply dummy text of the printing and typesetting industry. Lorem Ipsum has been the industry's standard dummy text.</p>
  </div>

  <div class="abs service" style="left:787px;top:169px">
    <div class="service-icon">
      <svg width="70" height="64" viewBox="0 0 70 64" fill="none" stroke="#fff" stroke-width="3">
        <path d="M18 30a12 12 0 0 1 2-24 16 16 0 0 1 30 4 10 10 0 0 1 2 20z"/>
        <rect x="20" y="34" width="30" height="8"/><rect x="20" y="44" width="30" height="8"/><rect x="20" y="54" width="30" height="8"/>
      </svg>
    </div>
    <h3>Cloud Services of Data<br>Backups</h3>
    <p>Lorem Ipsum is simply dummy text of the printing and typesetting industry. Lorem Ipsum has been the industry's standard dummy text.</p>
  </div>

  <a class="btn" style="left:160px;top:509px;width:169px;height:53px">Learn More</a>
  <a class="btn" style="left:516px;top:509px;width:169px;height:53px">Learn More</a>
  <a class="btn" style="left:872px;top:509px;width:169px;height:53px">Learn More</a>
</section>

<section class="about">
  <div class="abs about-photo" role="img" aria-label="Dark photo of a keyboard with a stethoscope lying on it"></div>
  <h2 class="abs center section-title" style="top:55px;color:#fff">Who <span>we are</span></h2>
  <p class="abs center section-sub" style="top:112px;color:#fff">Lorem Ipsum is simply dummy text of the printing and typesetting industry.</p>
  <div class="abs about-laptop" role="img" aria-label="Laptop showing a dental x-ray image"></div>
  <p class="abs about-text">Lorem Ipsum is simply dummy text of the printing and typesetting industry. Lorem Ipsum has been the industry's standard dummy text ever since the 1500s, when an unknown printer took a galley of type and scrambled it to make a type specimen book. It has survived not only five centuries, but also the leap into electronic typesetting, remaining essentially unchanged.</p>
  <a class="btn" style="left:667px;top:367px;width:156px;height:52px">Learn More</a>
</section>

<section class="blog">
  <h2 class="abs center section-title" style="top:55px">Latest <span>Blog</span></h2>
  <p class="abs center section-sub" style="top:116px">Lorem Ipsum is simply dummy text of the printing and typesetting industry.</p>

  <article class="abs post" style="left:79px">
    <div class="post-photo" role="img" aria-label="Photo of dentists reviewing an x-ray on a screen" style="background:linear-gradient(135deg,#8fb3cf,#3f6f98 60%,#c9d4dc)"></div>
    <h4>Lorem Ipsum is simply dummy text of the printing</h4>
    <div class="post-meta"><span>&#128172; 2</span><span class="sep">/</span><span>Lena Hartwell</span><span class="sep">/</span><span>April 12th 2016</span></div>
    <p>Lorem Ipsum is simply dummy text of the printing and typesetting industry.</p>
  </article>

  <article class="abs post" style="left:432px">
    <div class="post-photo" role="img" aria-label="Close-up photo of white pearls on a pale surface" style="background:linear-gradient(135deg,#e8e9ea,#bfc3c6 55%,#f2f2f2)"></div>
    <h4>Lorem Ipsum is simply dummy text of the printing</h4>
    <div class="post-meta"><span>&#128172; 2</span><span class="sep">/</span><span>Lena Hartwell</span><span class="sep">/</span><span>April 12th 2016</span></div>
    <p>Lorem Ipsum is simply dummy text of the printing and typesetting industry.</p>
  </article>

  <article class="abs post" style="left:788px">
    <div class="post-photo" role="img" aria-label="Photo of medical staff in white coats at a computer" style="background:linear-gradient(135deg,#dfe6ec,#9fb7c9 55%,#eef1f3)"></div>
    <h4>Lorem Ipsum is simply dummy text of the printing</h4>
    <div class="post-meta"><span>&#128172; 2</span><span class="sep">/</span><span>Lena Hartwell</span><span class="sep">/</span><span>April 12th 2016</span></div>
    <p>Lorem Ipsum is simply dummy text of the printing and typesetting industry.</p>
  </article>
</section>

<section class="clients">
  <div class="abs clients-photo" role="img" aria-label="Dim photo of a dental treatment room with a patient chair"></div>
  <h2 class="abs center section-title" style="top:50px;color:#fff">What <span>clients say</span></h2>
  <p class="abs center section-sub" style="top:106px;color:#fff">Lorem Ipsum is simply dummy text of the printing and typesetting industry.</p>
  <div class="abs center" style="top:190px;font-family:'Raleway',Arial,sans-serif;font-weight:600;font-size:22px;color:#f2c230">Little Grins Dental</div>
  <div class="abs center client-name">LITTLE GRINS DENTAL CARE</div>
  <div class="abs center client-role">Dr. Mara Quinlan</div>
  <div class="abs quote-mark" style="left:172px;top:322px">&#8220;</div>
  <p class="abs quote">Lorem Ipsum is simply dummy text of the printing and typesetting industry. Lorem Ipsum has been the industry's standard dummy text ever since the 1500s, when an unknown printer took a galley of type and scrambled it to make a type specimen book.It has survived not only five centuries, but also the leap into electronic typesetting.</p>
  <div class="abs quote-mark" style="left:970px;top:362px">&#8221;</div>
  <svg class="abs" style="left:26px;top:240px" width="20" height="34" viewBox="0 0 20 34"><path d="M17 2 3 17l14 15" fill="none" stroke="#fff" stroke-width="3"/></svg>
  <svg class="abs" style="left:1154px;top:240px" width="20" height="34" viewBox="0 0 20 34"><path d="M3 2l14 15L3 32" fill="none" stroke="#fff" stroke-width="3"/></svg>
</section>

<section class="partners">
  <span>Tessel Dental Spa</span>
  <span>Valewood Dental</span>
  <span>Corbin Smiles</span>
  <span>Hearthside Dental</span>
  <span>Pellam Ortho</span>
  <span>Norrow Dental Group</span>
</section>

<section class="newsletter">
  <div class="abs newsletter-photo" role="img" aria-label="Dark photo of hands holding a tablet"></div>
  <h2 class="abs center section-title" style="top:50px;color:#fff">Subscribe to <span>Newsletter</span></h2>
  <p class="abs center" style="top:122px;font-size:16px;line-height:26px;color:#fff">Subscribe to our Newsletter to get Latest Updates &amp; News<br>About Your System</p>
  <div class="abs nl-input">Enter E-Mail Id</div>
  <a class="btn" style="left:725px;top:211px;width:156px;height:53px">Subscribe</a>
</section>

<section class="contact">
  <h2 class="abs center section-title" style="top:48px">Contact <span>Us</span></h2>
  <div class="abs contact-info" style="top:128px">
    <svg width="30" height="38" viewBox="0 0 30 38"><path d="M15 2a12 12 0 0 0-12 12c0 9 12 22 12 22s12-13 12-22A12 12 0 0 0 15 2z" fill="none" stroke="var(--red)" stroke-width="2.5"/><circle cx="15" cy="14" r="4.5" fill="none" stroke="var(--red)" stroke-width="2.5"/></svg>
    <p style="font-size:15px;line-height:22px;margin-top:10px">123 Building Name, Area, City, Country<br>-Zipcode</p>
  </div>
  <div class="abs contact-info" style="top:245px">
    <svg width="44" height="34" viewBox="0 0 44 34"><path d="M8 4c-4 2-5 7-1 13s10 12 16 13c4 1 6-2 6-4l-5-4-4 3c-3-1-7-5-8-8l3-4-4-6z" fill="var(--red)"/><ellipse cx="32" cy="14" rx="10" ry="7" fill="none" stroke="var(--red)" stroke-width="2.5"/></svg>
    <p style="margin-top:14px">(123) 4567-890</p>
  </div>
  <div class="abs contact-info" style="top:362px">
    <svg width="36" height="32" viewBox="0 0 36 32"><rect x="3" y="9" width="30" height="20" fill="none" stroke="var(--red)" stroke-width="2.5"/><path d="M3 9l15 11 15-11M8 9V3h20v6" fill="none" stroke="var(--red)" stroke-width="2.5"/></svg>
    <p style="margin-top:10px">info@brimlowortholink.com</p>
  </div>

  <div class="field" style="left:435px;top:137px;width:332px;height:51px">Name</div>
  <div class="field" style="left:786px;top:137px;width:335px;height:51px">E-Mail Address</div>
  <div class="field" style="left:435px;top:197px;width:686px;height:51px">Dental</div>
  <div class="field" style="left:435px;top:261px;width:686px;height:100px">Message</div>
  <a class="btn" style="left:435px;top:385px;width:686px;height:50px;font-size:18px">Submit</a>
</section>

<footer class="site-footer">
  <div class="abs foot-brand">Brimlow OrthoLink IT</div>
  <div class="abs socials"><span></span><span></span><span></span><span></span></div>
  <p class="abs copyright">&copy; <b>BRIMLOW ORTHOLINK IT</b> - 2016. All Rights Reserved.</p>

  <div class="abs foot-col" style="left:409px;top:36px">
    <h5>Main Navigation</h5>
    <ul><li class="on">Home</li><li>About</li><li>Support</li><li>Blog</li></ul>
  </div>
  <div class="abs foot-col" style="left:519px;top:67px">
    <ul><li>Services</li><li>Clients</li><li>Contact</li></ul>
  </div>
  <div class="abs foot-col" style="left:651px;top:36px">
    <h5>Services</h5>
    <ul><li>Audio Visual</li><li>Computer System &amp; Network</li><li>Cloud Services of Data Backups</li></ul>
  </div>
  <div class="abs foot-col" style="left:915px;top:36px">
    <h5>Sitemap</h5>
    <ul><li>Privacy Policy</li><li>Terms of Use</li><li>Conditions</li></ul>
  </div>
</footer>

</body>
</html>
```